-Photo booth rental Web Design Project

Our business is a small photo booth rental service serving the capital region and surrounding areas. The photo booth is a portable booth that fits up to 10 guest. I am looking for a website that will have social media capabilities and also private log ins for clients to view their photo albums online after their event. We provide full service photo booth rentals for all types of parties. I am looking for something fun and unique but also professional and I am also looking to maybe somehow incorporate the age of the photo booth which was invented in 1888. I do not have the photos of our photo booth available because we are just starting up and I wanted to get everything together first but I will provide stock photo booth pictures .Thank you for your patience i know it wont be an easy task with out those things. I added a word document describing information i will need on our website, i am looking for a home page, contact us and book an event page, online gallery page, and pricing. If you need any more information please feel free to contact me. Thanks for your help and I look forward to working with you.

Target Market(s)

For everyone from brides to be for their weddings or private parties, corporate parties, school dances, charity events, community events ect

Industry/Entity Type

Business

Requirements
Nice to have
• social media sharing

```html
<!DOCTYPE html>
<html lang="en">
<head>
<meta charset="utf-8">
<title>Giggle Frames photo booth</title>
<link href="https://fonts.googleapis.com/css2?family=Bebas+Neue&family=Open+Sans:wght@400;600&family=Titillium+Web:wght@400;600&display=swap" rel="stylesheet">
<style>
:root{
  --brown:#412a1e;
  --red:#de403b;
  --grey:#e1e1e1;
  --text:#555;
  --light:#fff;
  --dark:#2b2b2b;
}
*{margin:0;padding:0;box-sizing:border-box}
html,body{width:1200px;height:2198px;overflow:hidden;background:var(--light)}
body{position:relative;font-family:"Open Sans",sans-serif;color:var(--text)}
.abs{position:absolute}
h1,h2,h3{font-weight:400}

/* header */
.brand{left:100px;top:40px;font-family:"Titillium Web",sans-serif;font-weight:600;color:var(--brown);font-size:34px;line-height:32px;letter-spacing:-1px}
.brand span{display:block;padding-left:52px}
.nav{left:607px;top:48px;display:flex;align-items:center;font-size:13px;color:var(--dark)}
.nav a{color:inherit;text-decoration:none;margin-right:34px;line-height:44px}
.nav a.active{background:var(--red);color:var(--light);padding:0 25px;border-radius:3px;font-weight:600;margin-right:18px}
.nav a:last-child{margin-right:0}

/* hero */
.hero{left:0;top:141px;width:1200px;height:581px;background:var(--brown)}
.slider{left:100px;top:168px;width:1000px;height:526px;background:var(--light);padding:6px}
.slide{width:100%;height:100%;background:linear-gradient(120deg,#8a7466 0%,#5b4a40 45%,#c9c2bb 75%,#3c3430 100%)}
.arrow{width:37px;height:67px;background:var(--light);display:flex;align-items:center;justify-content:center}
.arrow.prev{left:105px;top:409px}
.arrow.next{left:1052px;top:409px}
.dots{left:549px;top:668px;width:104px;height:26px;background:var(--light);border-radius:10px 10px 0 0;display:flex;justify-content:center;align-items:center;gap:8px}
.dots i{width:12px;height:12px;border-radius:50%;border:1.5px solid #5c7fb0;display:block}
.dots i.on{background:var(--red);border-color:var(--red)}

/* welcome */
.welcome-title{left:100px;top:752px;font-family:"Titillium Web",sans-serif;font-size:29px;color:var(--dark)}
.welcome-text{left:100px;top:800px;width:674px;font-size:11.4px;line-height:24px;color:var(--text)}
.booth{left:857px;top:730px;width:208px;height:255px;background:linear-gradient(160deg,#2a2a2a 0%,#3a1a1a 50%,#c23 65%,#d8d0c8 100%)}

/* pricing */
.pricing{left:0;top:1040px;width:1200px;height:567px;background:var(--grey)}
.pricing-title{left:0;top:1066px;width:1200px;text-align:center;font-family:"Titillium Web",sans-serif;font-size:29px;color:var(--dark)}
.plan{top:1127px;width:308px;height:414px;background:var(--light);border-radius:4px;overflow:hidden;box-shadow:0 0 0 1px #c9c9c9}
.plan-head,.plan-price{background:var(--brown);color:var(--light);font-family:"Bebas Neue",sans-serif;text-align:center}
.plan-head{height:63px;line-height:66px;font-size:29px}
.plan-price{position:absolute;left:0;bottom:0;width:100%;height:60px;line-height:62px;font-size:30px}
.plan.featured .plan-head,.plan.featured .plan-price{background:var(--red)}
.plan ul{list-style:none;text-align:center;font-size:15px;line-height:30px;color:#666;padding:16px 40px 0}

/* promo banner */
.promo{left:100px;top:1660px;width:1000px;height:94px;display:flex;font-family:"Bebas Neue",sans-serif;font-size:28px;color:var(--light)}
.promo-items{background:var(--red);width:769px;line-height:98px;padding-left:43px}
.promo-deposit{background:var(--brown);flex:1;line-height:98px;text-align:center}

/* gallery */
.gallery-title{left:100px;top:1811px;font-family:"Titillium Web",sans-serif;font-size:23px;color:var(--dark)}
.gallery-nav{left:1066px;top:1809px}
.thumb{top:1865px;height:167px;display:flex;align-items:center;justify-content:center}
.t1{left:100px;width:309px;background:linear-gradient(135deg,#8d7a5e,#b9a583 60%,#6e5d44)}
.t2{left:444px;width:311px;background:linear-gradient(180deg,#8fa3b4 0%,#c8ced2 40%,#4d4f52 100%)}
.t3{left:790px;width:310px;background:linear-gradient(90deg,#1b1b1b,#3c3c3c 50%,#d6d6d6 75%,#222)}

/* footer */
.footer{left:0;top:2070px;width:1200px;height:128px;background:var(--brown);color:var(--light)}
.foot-links{left:101px;top:2107px;font-size:11px;color:var(--light)}
.foot-links a{color:inherit;text-decoration:none}
.foot-links b{font-weight:400;margin:0 6px}
.copy{left:100px;top:2133px;font-size:11px;color:var(--light)}
.social{top:2114px;width:36px;height:36px;border-radius:50%;background:#d9d9d9}
</style>
</head>
<body>

<header>
  <div class="abs brand">Giggle Frames<span>photo booth</span></div>
  <nav class="abs nav">
    <a class="active" href="#">Home</a>
    <a href="#">Pricing</a>
    <a href="#">Contact us</a>
    <a href="#">Book an event</a>
    <a href="#">Client log in</a>
  </nav>
</header>

<section>
  <div class="abs hero"></div>
  <div class="abs slider"><div class="slide" role="img" aria-label="Two photographers shooting with cameras on a city street"></div></div>
  <div class="abs arrow prev"><svg width="12" height="18" viewBox="0 0 12 18"><path d="M9 3 3 9l6 6" fill="none" stroke="#de403b" stroke-width="3.5"/></svg></div>
  <div class="abs arrow next"><svg width="12" height="18" viewBox="0 0 12 18"><path d="M3 3l6 6-6 6" fill="none" stroke="#de403b" stroke-width="3.5"/></svg></div>
  <div class="abs dots"><i class="on"></i><i></i><i></i></div>
</section>

<section>
  <h1 class="abs welcome-title">Welcome To Giggle Frames photo booth</h1>
  <p class="abs welcome-text">Lorem ipsum dolor sit amet, consectetuer adipiscing elit, sed diam nonummy nibh euismod tincidunt ut laoreet dolore magna aliquam erat volutpat. Ut wisi enim ad minim veniam, quis nostrud exerci tation ullamcorper suscipit lobortis nisl ut aliquip ex ea commodo consequat. Lorem ipsum dolor sit amet, consectetuer adipiscing elit, sed diam nonummy nibh euismod tincidunt ut laoreet dolore magna aliquam erat volutpat. Ut wisi enim ad minim veniam, quis nostrud exerci tation ullamcorper suscipit lobortis nisl ut aliquip ex ea commodo consequat. Lorem ipsum dolor sit amet, consectetuer adipiscing elit, sed diam nonummy nibh euismod tincidunt ut laoreet dolore magna aliquam erat volutpat. Ut wisi enim ad minim veniam, quis nostrud exerci tation ullamcorper suscipit lobor</p>
  <div class="abs booth" role="img" aria-label="Couple standing beside a black and red photo booth"></div>
</section>

<section>
  <div class="abs pricing"></div>
  <h2 class="abs pricing-title">Pricing information</h2>
  <div class="abs plan" style="left:100px">
    <div class="plan-head">Standard</div>
    <ul><li>3 hours of service</li><li>Set up &amp; removal</li><li>Professional &amp; friendly booth attendant</li><li>Dvd or usb flash drive of picture</li><li>Guestbook</li><li>Unlimited prints</li><li>Online gallery</li></ul>
    <div class="plan-price">$675</div>
  </div>
  <div class="abs plan featured" style="left:450px">
    <div class="plan-head">Ultimate</div>
    <ul><li>3 hours of service</li><li>Set up &amp; removal</li><li>Professional &amp; friendly booth attendant</li><li>Dvd or usb flash drive of picture</li><li>Guestbook</li><li>Unlimited prints</li><li>Online gallery</li></ul>
    <div class="plan-price">$675</div>
  </div>
  <div class="abs plan" style="left:791px">
    <div class="plan-head">Extreme</div>
    <ul><li>3 hours of service</li><li>Set up &amp; removal</li><li>Professional &amp; friendly booth attendant</li><li>Dvd or usb flash drive of picture</li><li>Guestbook</li><li>Unlimited prints</li><li>Online gallery</li></ul>
    <div class="plan-price">$675</div>
  </div>
</section>

<div class="abs promo">
  <div class="promo-items">Magnet photo strip frames, stand up acrylic photo strip frames,</div>
  <div class="promo-deposit">Only $100 deposit</div>
</div>

<section>
  <h3 class="abs gallery-title">Gallery</h3>
  <svg class="abs gallery-nav" width="36" height="24" viewBox="0 0 36 24"><path d="M12 5 6 12l6 7M24 5l6 7-6 7" fill="none" stroke="#666" stroke-width="3.5"/></svg>
  <div class="abs thumb t1" role="img" aria-label="Photographer shooting a bride on rocky ground">
    <svg width="42" height="42" viewBox="0 0 42 42"><circle cx="21" cy="21" r="20" fill="#de403b" opacity=".85"/><rect x="11" y="15" width="20" height="14" rx="2" fill="none" stroke="#fff" stroke-width="2"/><circle cx="21" cy="22" r="4" fill="none" stroke="#fff" stroke-width="2"/><rect x="17" y="12" width="8" height="3" fill="#fff"/></svg>
  </div>
  <div class="abs thumb t2" role="img" aria-label="Two photographers on a rocky shoreline">
    <svg width="42" height="42" viewBox="0 0 42 42"><circle cx="21" cy="21" r="20" fill="#de403b" opacity=".85"/><rect x="11" y="15" width="20" height="14" rx="2" fill="none" stroke="#fff" stroke-width="2"/><circle cx="21" cy="22" r="4" fill="none" stroke="#fff" stroke-width="2"/><rect x="17" y="12" width="8" height="3" fill="#fff"/></svg>
  </div>
  <div class="abs thumb t3" role="img" aria-label="Photographer working in a studio with softbox lights">
    <svg width="42" height="42" viewBox="0 0 42 42"><circle cx="21" cy="21" r="20" fill="#de403b" opacity=".85"/><rect x="11" y="15" width="20" height="14" rx="2" fill="none" stroke="#fff" stroke-width="2"/><circle cx="21" cy="22" r="4" fill="none" stroke="#fff" stroke-width="2"/><rect x="17" y="12" width="8" height="3" fill="#fff"/></svg>
  </div>
</section>

<footer>
  <div class="abs footer"></div>
  <div class="abs foot-links"><a href="#">Home</a><b>|</b><a href="#">About us</a><b>|</b><a href="#">Counselling</a><b>|</b><a href="#">Workshop</a><b>|</b><a href="#">Contact us</a></div>
  <div class="abs copy">Content copyright 2014. Brightlane. All rights reserved.</div>
  <div class="abs social" style="left:973px" aria-label="Social link 1"></div>
  <div class="abs social" style="left:1018px" aria-label="Social link 2"></div>
  <div class="abs social" style="left:1062px" aria-label="Social link 3"></div>
</footer>

</body>
</html>
```